Advertising Portal Needs eBrochure

Hi Crowders! Our advertising portal, which focus on the new launches property, needs an online brochure to promote to potential advertisers the benefits of advertising their projects with us. These advertisers will be mainly real estate developers and agencies.

WHAT WE LOOKING FOR
We do not want over-fanciful designs that makes the content hard to read. The use of illustrations and graphics/symbols related to covered topics are encouraged. The overall design should portrait our advertising efficiency through online and social media means. Our website - www.brightkeyhomes.sg.

For draft purposes, just do up the front page, back page, and few inner pages, preferably to include one illustration chart (either on page 7/8). Size wise probably A5 portrait or landscape, for future printing into a booklet.

WORK COMPLETION AND PAYMENT
The $500 stated here is 50% of the payment. Upon getting a desired draft design, we will need you to work on the full content with slight amendments along the way. Once done, we will be paying the balance $500, and we will need the pdf file as well as the work file.

Let your design juice flow, and hope we can work with you!
Updates

Hi Crowders! Thank you for your submissions. We are closing the project as we've decided on a design. It's a pity we can only select one design, as there are a number of good works. Hope we will have a chance to work together on our upcoming projects. Cheers =)

Target Market(s)

Real estate developers, real estate agencies, and perhaps to an extent, individual property sales agent.

Industry/Entity Type

Advertising

Requirements
Should not have
• We prefer not to have much real people kind of stock images. Try not to use images from our portal as we do not have the ownerships. Instead, you can use stock images of property developments artist impression that gives a similar feel.

```html
<!DOCTYPE html>
<html lang="en">
<head>
<meta charset="utf-8">
<title>Keystone Reach LLP – Back Cover</title>
<link href="https://fonts.googleapis.com/css2?family=Noto+Serif:wght@400;700&display=swap" rel="stylesheet">
<style>
  :root {
    --page-white: #ffffff;
    --bg-top: #d3e6da;
    --bg-mid: #e6ecea;
    --bg-low: #c9cfcd;
    --bg-bottom: #b9c3be;
    --brand-green: #3aaa47;
    --text-dark: #1b1b1b;
    --tab-light: #28bf9c;
    --tab-dark: #3f8c7f;
    --tab-fold: #2f7a6c;
  }
  * { margin: 0; padding: 0; box-sizing: border-box; }
  html, body {
    width: 1200px;
    height: 846px;
    overflow: hidden;
    background: var(--page-white);
  }
  .canvas {
    position: relative;
    width: 1200px;
    height: 846px;
  }
  .back-cover {
    position: absolute;
    left: 0;
    top: 0;
    width: 1140px;
    height: 846px;
    background:
      radial-gradient(ellipse 70% 55% at 45% 35%, rgba(236,240,239,0.9), rgba(236,240,239,0) 70%),
      linear-gradient(to bottom, var(--bg-top) 0%, var(--bg-mid) 35%, var(--bg-mid) 50%, var(--bg-low) 80%, var(--bg-bottom) 100%);
  }
  .back-cover::after {
    content: "";
    position: absolute;
    inset: 0;
    background: linear-gradient(to top, rgba(200,222,210,0.6), rgba(200,222,210,0) 12%);
  }
  .edge-tab {
    position: absolute;
    left: 1086px;
    top: 514px;
    width: 72px;
    height: 86px;
  }
  .contact-block {
    position: absolute;
    right: 148px;
    top: 512px;
    text-align: right;
    font-family: "Noto Serif", Georgia, serif;
    color: var(--text-dark);
    font-size: 16.5px;
    line-height: 27.3px;
    z-index: 1;
  }
  .company-name {
    font-size: 23px;
    font-weight: 700;
    color: var(--brand-green);
    letter-spacing: 0.3px;
    line-height: 32px;
    margin-bottom: 1px;
  }
  .address { margin-bottom: 27px; }
  .label { font-weight: 700; }
</style>
</head>
<body>
<div class="canvas">
  <div class="back-cover"></div>

  <svg class="edge-tab" viewBox="0 0 72 86" aria-hidden="true">
    <defs>
      <linearGradient id="tabFill" x1="0" y1="0" x2="1" y2="0">
        <stop offset="0" stop-color="var(--tab-dark)"/>
        <stop offset="0.55" stop-color="var(--tab-light)"/>
        <stop offset="1" stop-color="var(--tab-light)"/>
      </linearGradient>
    </defs>
    <polygon points="54,2 69,14 54,14" fill="var(--tab-fold)"/>
    <polygon points="2,49 36,14 69,14 69,84 36,84" fill="url(#tabFill)"/>
  </svg>

  <div class="contact-block">
    <h1 class="company-name">KEYSTONE REACH LLP</h1>
    <p class="address">42 Alder Park Road #05-11,<br>Parkside Hub.<br>Singapore 579812</p>
    <p><span class="label">Mobile:</span> +(65) 91234578</p>
    <p><span class="label">Office:</span> +(65) 65502143</p>
    <p><span class="label">Email:</span> admin@brightkeyhomes.sg</p>
    <p><span class="label">Web:</span> www.brightkeyhomes.sg</p>
  </div>
</div>
</body>
</html>
```